Brand new letterhead, business card, email signature etc.

We are a financial company in London, UK. Our website is www.marlowvane.com. We're wanting a complete remodel of the company colours, letter head, business cards, email signatures, etc. Looking to keep the same font for the company name. I have upload a colour palette that we want to work with. We're looking for company letterhead for outgoing letters/ correspondence, letterhead for internal documentation, email signatures, e-letters. etc. Ultimately we will redesign the entire website also. It is important that our clients get a strong, secure, warm, trustworthy, solid feeling and first impression.
Updates

Designs look the same

Target Market(s)

Institutional investors, (ultra) high net worth individuals

Industry/Entity Type

Finance, Invesments banking.

Font styles to use
Other font styles liked:
• Current font is "Champagne & Limousines"

Requirements
Must have
• Must use the colours provided on the PDF uploaded to the portal. The purple = main colour. The red = accent colour.
Nice to have
• Nice to use same font as now for the company name "Corvane". Font is "Champagne & Limousines". Nice to have some reference to the old logo flower, but only subtle.
Should not have
• Do not use the colour red from our website. Use the colours provided on the colour palette PDF that I uploaded in the portal.

```html
<!DOCTYPE html>
<html lang="en">
<head>
<meta charset="utf-8">
<title>Corvane – Business Card</title>
<link rel="stylesheet" href="https://fonts.googleapis.com/css2?family=Josefin+Sans:wght@300&family=Montserrat:wght@400;700&display=swap">
<style>
  :root {
    --backdrop: #232323;
    --brand-purple: #4a2660;
    --card-dark: #1d1523;
    --accent-red: #c8283c;
    --wordmark-light: #f1dccb;
    --ink-white: #ffffff;
    --decor-tone: #2c2133;
  }
  * { box-sizing: border-box; margin: 0; padding: 0; }
  html, body {
    width: 1200px; height: 780px; overflow: hidden;
    background: var(--backdrop);
  }
  .canvas { position: relative; width: 1200px; height: 780px; }

  .card {
    position: absolute; width: 560px; height: 320px;
    box-shadow: 0 18px 40px rgba(0,0,0,.55);
  }
  .card--front { left: 110px; top: 70px; background: var(--brand-purple); }
  .card--back {
    left: 530px; top: 390px; background: var(--card-dark);
    border-bottom: 5px solid var(--accent-red);
  }

  .brand { position: absolute; display: flex; align-items: center; gap: 20px; }
  .brand__square { display: block; border: 1.5px solid currentColor; }
  .brand__name {
    font-family: "Josefin Sans", sans-serif; font-weight: 300;
    text-transform: uppercase; letter-spacing: .28em; line-height: 1;
  }
  .card--front .brand { left: 70px; top: 124px; color: var(--wordmark-light); }
  .card--front .brand__square { width: 72px; height: 72px; }
  .card--front .brand__name { font-size: 46px; padding-top: 8px; }

  .card--back .brand { left: 34px; top: 34px; color: var(--ink-white); }
  .card--back .brand__square { width: 52px; height: 52px; }
  .card--back .brand__name { font-size: 30px; padding-top: 6px; }

  .decor {
    position: absolute; right: 24px; top: 22px; width: 230px; height: 180px;
    border-radius: 50% 46% 40% 50%;
    background: radial-gradient(circle at 55% 45%, var(--decor-tone), var(--card-dark) 72%);
  }

  .contact { position: absolute; left: 34px; bottom: 28px; color: var(--ink-white); font-family: "Montserrat", sans-serif; }
  .contact__name { font-size: 27px; font-weight: 700; letter-spacing: -.01em; margin-bottom: 12px; }
  .contact__first { color: var(--accent-red); }
  .contact__role { color: var(--accent-red); font-weight: 400; font-size: 17px; margin-left: 6px; }
  .contact__row { font-size: 13px; display: flex; gap: 34px; margin-bottom: 6px; }
  .contact__address { font-size: 13px; }
  .label { color: var(--accent-red); margin-right: 4px; }

  .web {
    position: absolute; right: 30px; top: 214px;
    font-family: "Montserrat", sans-serif; font-size: 13px; color: var(--ink-white);
  }
</style>
</head>
<body>
<main class="canvas">
  <section class="card card--front" aria-label="Business card front">
    <div class="brand">
      <span class="brand__square"></span>
      <span class="brand__name">Corvane</span>
    </div>
  </section>

  <section class="card card--back" aria-label="Business card back">
    <div class="brand">
      <span class="brand__square"></span>
      <span class="brand__name">Corvane</span>
    </div>
    <div class="decor" role="img" aria-label="Large embossed flower decoration, tone on tone"></div>
    <p class="web"><span class="label">W:</span>www.marlowvane.com</p>
    <div class="contact">
      <p class="contact__name"><span class="contact__first">Elena</span> Marsh<span class="contact__role">CEO</span></p>
      <p class="contact__row">
        <span><span class="label">T:</span>+44 20 7946 0321</span>
        <span><span class="label">E:</span>info@marlowvane.com</span>
      </p>
      <p class="contact__address">18 Linden Court, Suite 3, London EC2V 7QP</p>
    </div>
  </section>
</main>
</body>
</html>
```